Medical centre needs a business card

We are a medcial centre in Australia, needing a new business card. Our demographic is low working class families. We are going to be renovating our premises to modernise the look and also had a new logo done a few months ago representing quality and community, and now need to update our cards. It needs to be doubled sided, with logo and contact details on the front, and appointment details on the back. . Needs to be modern and simple, easy to read. <br/><br/>Name: Kindle Grove Medical Centre <br/>Address: 512 Parmley Rd (Cnr Parmley Rd & Osgood Creek Rd),<br/>Tindarra Court Shopping Centre, Paralowie, SA 5108<br/>Ph: 08 8461 3072<br/>Tag line: Where your wellbeing comes first<br/>Website: www.kindlegrovemedicalcentre-example.com.au<br/>Online bookings also available<br/><br/>(On the back, to have 3 lines of appointments that can be written in.<br/>Day, date, time)<br/><br/>Your next appointment is on<br/>Can try “M T W Th F Sa Su _________________ at ____________ am/pm” or other combinations <br/>Please advise as soon as possible if unable to attend<br/>Cancellation fees apply if less than 2 hrs notice<br/>Online appointments available (please highlight this option by either by position, colour or font)

Target Market(s)

Lower social economic working class, young families to seniors

Industry/Entity Type

Medical Centre

Contact Information for Business Card

Kindle Grove Medical Centre
512 Parmley Rd (Cnr Parmley Rd & Osgood Creek Drive)
Tindarra Court Shopping Centre
Marrowfield SA 5921
Ph: 08 8461 3072
www.kindlegrovemedicalcentre-example.com.au
Tagline line: where your wellbeing comes first
Back side is for appointments
Your next appointment is with Dr ______________
Day/date/time (Please give 3 lines of appointments)
Please advise as soon as possible if unable to attend
Cancellation fees apply if less than 2 hours notice
Online appointments available
Book online easily and conveniently (please highlight online appointments)

Font styles to use
Serif
Sans Serif

Colors

Designer to choose colors to be used in the design.

Requirements
Must have
• Modern and simple
• Easy to ready
• Induces a wellbeing feeling
• Incorporate our logo colours and feel from logo
• Induces feeling of stability and security
Nice to have
• Attract attention
• Pleasant to look at
• Feeling of innovation
Should not have
• Loud clashing colours
• Overly luxurious feeling
• Overly artistic

```html
<!DOCTYPE html>
<html lang="en">
<head>
<meta charset="utf-8">
<title>Kindle Grove Medical Centre – Business Card</title>
<link rel="stylesheet" href="https://fonts.googleapis.com/css2?family=Source+Sans+3:wght@400;600;700&display=swap">
<style>
  :root {
    --blue: #1673bf;
    --blue-dark: #0f5fa6;
    --blue-light: #22a0dc;
    --green: #9cc83c;
    --ink: #222;
    --rule: #888;
    --paper: #ffffff;
    --backdrop: #2a2a2a;
  }
  * { box-sizing: border-box; margin: 0; padding: 0; }
  html, body { width: 1200px; height: 1021px; overflow: hidden; }
  body {
    background: var(--backdrop);
    font-family: "Source Sans 3", Arial, sans-serif;
    color: var(--ink);
    position: relative;
  }
  .card {
    position: absolute;
    left: 200px;
    width: 800px;
    height: 457px;
    background: var(--paper);
    overflow: hidden;
  }
  .card--back { top: 40px; }
  .card--front { top: 524px; }

  /* Back: appointment side */
  .appointment-tab {
    position: absolute;
    left: 390px; top: 0;
    width: 320px; height: 52px;
    background: var(--green);
    border-radius: 0 0 10px 10px;
    color: #fff;
    font-weight: 600;
    font-size: 21px;
    letter-spacing: 1px;
    text-transform: uppercase;
    display: flex; align-items: center; justify-content: center;
  }
  .appointment-form {
    position: absolute;
    left: 50px; right: 50px; top: 72px;
    font-size: 18px;
  }
  .form-row { display: flex; align-items: flex-end; gap: 8px; height: 46px; }
  .fill-line { flex: 1; border-bottom: 1px solid var(--rule); height: 20px; }
  .fill-line--short { flex: 0 0 150px; }
  .days { display: flex; justify-content: space-between; height: 40px; align-items: center; margin-top: 6px; }
  .day { display: flex; align-items: center; gap: 8px; }
  .checkbox { width: 22px; height: 18px; border: 2px solid var(--green); }
  .notice {
    position: absolute;
    left: 0; right: 0; top: 320px;
    text-align: center;
    font-size: 18px;
    line-height: 1.3;
  }
  .band {
    position: absolute;
    left: 0; right: 0; bottom: 0;
    height: 48px;
    background: linear-gradient(90deg, var(--blue-dark), var(--blue));
    color: #fff;
    display: flex; align-items: center; justify-content: center;
    font-size: 19px;
    gap: 8px;
  }
  .band__highlight { color: var(--green); font-weight: 600; }

  /* Front: contact side */
  .brand {
    position: absolute;
    left: 48px; top: 62px;
    display: flex; align-items: center; gap: 12px;
    color: var(--blue);
    font-weight: 700;
    font-size: 26px;
  }
  .brand__mark { width: 22px; height: 22px; background: var(--blue); }
  .name-tab {
    position: absolute;
    left: 0; top: 148px;
    width: 18px; height: 48px;
    background: var(--green);
    border-radius: 0 6px 6px 0;
  }
  .person { position: absolute; left: 48px; top: 140px; }
  .person__name { color: var(--blue); font-weight: 700; font-size: 30px; line-height: 1.1; }
  .person__role { font-size: 20px; }
  .contact {
    position: absolute;
    left: 48px; top: 232px;
    font-size: 19px;
    line-height: 1.3;
  }
  .contact__org { color: var(--blue); }
  .contact__line { display: flex; align-items: center; gap: 8px; }
  .contact__line svg { flex: none; }
  .decoration {
    position: absolute;
    left: 520px; right: 0; top: 110px; bottom: 0;
    border-radius: 18px 0 0 0;
    background: linear-gradient(160deg, var(--blue-light) 0%, var(--blue) 40%, var(--green) 75%, #b3d65e 100%);
  }
  .band--front {
    justify-content: flex-start;
    padding-left: 48px;
    color: var(--green);
    font-size: 21px;
    text-transform: uppercase;
    height: 52px;
  }
</style>
</head>
<body>

<section class="card card--back" aria-label="Appointment side">
  <div class="appointment-tab">Your next appointment</div>
  <div class="appointment-form">
    <div class="form-row"><span>Dr.:</span><span class="fill-line"></span></div>
    <div class="days">
      <span class="day"><span class="checkbox"></span>Mon</span>
      <span class="day"><span class="checkbox"></span>Tue</span>
      <span class="day"><span class="checkbox"></span>Wed</span>
      <span class="day"><span class="checkbox"></span>Thu</span>
      <span class="day"><span class="checkbox"></span>Fri</span>
      <span class="day"><span class="checkbox"></span>Sat</span>
      <span class="day"><span class="checkbox"></span>Sun</span>
    </div>
    <div class="form-row"><span>Date:</span><span class="fill-line"></span><span>Time:</span><span class="fill-line fill-line--short"></span><span>am/pm</span></div>
    <div class="form-row"><span>Date:</span><span class="fill-line"></span><span>Time:</span><span class="fill-line fill-line--short"></span><span>am/pm</span></div>
    <div class="form-row"><span>Date:</span><span class="fill-line"></span><span>Time:</span><span class="fill-line fill-line--short"></span><span>am/pm</span></div>
  </div>
  <p class="notice">Please advise as soon as possible if unable to attend<br>Cancellation fees apply if less than 2 hours notice</p>
  <div class="band">
    <span class="band__highlight">Online appointments available</span>
    <span>|</span>
    <span>Book online easily and conveniently</span>
  </div>
</section>

<section class="card card--front" aria-label="Contact side">
  <div class="brand"><span class="brand__mark"></span>Kindle Grove Medical Centre</div>
  <div class="name-tab"></div>
  <div class="person">
    <p class="person__name">Daniel Hartley</p>
    <p class="person__role">Founder</p>
  </div>
  <div class="contact">
    <p class="contact__org">Kindle Grove Medical Centre</p>
    <p>512 Parmley Rd (Cnr Parmley Rd &amp; Osgood Creek Drive)</p>
    <p>Tindarra Court Shopping Centre, Marrowfield SA 5921</p>
    <p class="contact__line">
      <svg width="16" height="16" viewBox="0 0 24 24" aria-hidden="true"><path fill="#9cc83c" d="M6.6 10.8a15 15 0 0 0 6.6 6.6l2.2-2.2a1 1 0 0 1 1-.25 11.4 11.4 0 0 0 3.6.57 1 1 0 0 1 1 1V20a1 1 0 0 1-1 1A17 17 0 0 1 3 4a1 1 0 0 1 1-1h3.5a1 1 0 0 1 1 1c0 1.25.2 2.45.57 3.57a1 1 0 0 1-.25 1z"/></svg>
      08 8461 3072
    </p>
    <p class="contact__line">
      <svg width="16" height="16" viewBox="0 0 24 24" aria-hidden="true" fill="none" stroke="#9cc83c" stroke-width="2"><circle cx="12" cy="12" r="9"/><path d="M3 12h18M12 3c3 3 3 15 0 18M12 3c-3 3-3 15 0 18"/></svg>
      www.kindlegrovemedicalcentre-example.com.au
    </p>
  </div>
  <div class="band band--front">Where your wellbeing comes first</div>
  <div class="decoration" role="img" aria-label="Large brand symbol decoration in blue and green"></div>
</section>

</body>
</html>
```